International Clinical Software Company needs a new business card design

We are looking for a new business card design for our company that has recently expanded into the UK market, making us a multinational company.
After having rebranded our website and produced a new style guide, we are looking for a business card that is creative and attention grabbing, while being consistent with the style and colour scheme used on the new website, www.plumvora.example
We produce care management technology for the aged care market, but the main aspect we aim to communicate is the human element of our software, and the way it assists in providing better care for aged people, and stronger relationships between aged people and the staff that care for them.
Our current business card is a dark green with gold text, which makes the text quite difficult to read, not very aesthetically appealing and the colour scheme looks quite dated.
We would like something fresh and modern, that can still be colourful but doesn't use large blocks of dark colour, and uses the colours within our logo.
Something tying in with the leaves that are used in our logo could work quite nicely, along with the Autumn/Fall colours of soft greens, yellows and reds (also in our existing logo). However also happy to look at fresh, completely out of the box ideas we may not have yet considered.
Target Market(s)
The people that receive this business card work in the aged card or health industry and are either corporate/management level staff or clinical (Registered Nurses, care workers etc.)
Industry/Entity Type
Health Product
Contact Information for Business Card
Company Name - BrindlewayCare
Company locations: United Kingdom, Australia, New Zealand
Staff Details:
Staff name: Derek Mallow
Staff job title: Executive Chairman
Staff email: d.mallow@plumvora.example
Office phone number: 01742 918576
Font styles to use
Other font styles liked:
- Calibri
Requirements
Must have
- Must include the BrindlewayCare brand name in it's current font
- Must include logo (3 leaves in gold circle)
- Must include Business Card Details
Nice to have
- Elements of gold
- White space
- Something autumn themed but not too cliched
Should not have
- No blue - used by a major competitor and we would like to differentiate from them
- Large blocks of dark green colour (the green that appears in our leaves on the logo on our current business card is the background colour and it is far too dark)

```html
<!DOCTYPE html>
<html lang="en">
<head>
<meta charset="utf-8">
<title>BrindlewayCare – Business Card</title>
<link rel="stylesheet" href="https://fonts.googleapis.com/css2?family=Open+Sans:wght@300;400;600&display=swap">
<style>
  :root {
    --page-bg: #ece9e2;
    --card-bg: #ffffff;
    --gold: #a89b6f;
    --gold-deep: #9c8f63;
    --gold-soft: #cfc6a6;
    --text-grey: #8c8c8c;
    --white: #ffffff;
  }
  * { margin: 0; padding: 0; box-sizing: border-box; }
  html, body {
    width: 1200px; height: 950px; overflow: hidden;
    background: var(--page-bg);
    font-family: "Open Sans", "Calibri", sans-serif;
  }
  .card {
    position: absolute; left: 100px; top: 185px;
    width: 1000px; height: 580px;
    background: var(--card-bg);
    border-radius: 28px;
    overflow: hidden;
    box-shadow: 0 10px 30px rgba(60, 50, 30, 0.18);
  }
  .name-band {
    position: absolute; left: 0; top: 62px;
    width: 520px; height: 128px;
    background: linear-gradient(90deg, var(--gold-deep) 0%, var(--gold) 45%, var(--gold-soft) 85%, rgba(207,198,166,0) 100%);
  }
  .person {
    position: absolute; left: 58px; top: 78px; color: var(--white);
  }
  .person-name { font-size: 42px; font-weight: 600; line-height: 1.1; white-space: nowrap; }
  .person-title { font-size: 26px; font-weight: 300; margin-top: 4px; white-space: nowrap; }
  .brand {
    position: absolute; left: 460px; top: 61px;
    display: flex; align-items: center; gap: 18px;
  }
  .brand-mark {
    width: 130px; height: 130px; border-radius: 50%;
    background: var(--white);
    border: 4px solid var(--gold);
    flex: none;
  }
  .brand-name {
    font-size: 42px; font-weight: 300; color: var(--gold);
    white-space: nowrap;
  }
  .contact-list {
    position: absolute; left: 215px; top: 270px;
    list-style: none; color: var(--text-grey);
    font-size: 26px; font-weight: 400; line-height: 44px;
  }
  .contact-list li { display: flex; align-items: center; gap: 16px; white-space: nowrap; }
  .contact-icon { width: 22px; height: 22px; flex: none; }
  .social-links {
    position: absolute; right: 58px; bottom: 70px;
    display: flex; gap: 10px;
  }
  .social-dot {
    width: 46px; height: 46px; border-radius: 50%;
    background: var(--gold);
  }
</style>
</head>
<body>
  <div class="card">
    <div class="name-band"></div>
    <div class="person">
      <div class="person-name">Derek Mallow</div>
      <div class="person-title">Executive Chairman</div>
    </div>

    <div class="brand">
      <div class="brand-mark"></div>
      <div class="brand-name">BrindlewayCare</div>
    </div>

    <ul class="contact-list">
      <li><svg class="contact-icon" viewBox="0 0 22 22"><circle cx="11" cy="11" r="4" fill="var(--gold)"/></svg>United Kingdom</li>
      <li><svg class="contact-icon" viewBox="0 0 22 22"><circle cx="11" cy="11" r="4" fill="var(--gold)"/></svg>Australia</li>
      <li><svg class="contact-icon" viewBox="0 0 22 22"><circle cx="11" cy="11" r="4" fill="var(--gold)"/></svg>New Zealand</li>
      <li><svg class="contact-icon" viewBox="0 0 22 22"><path d="M5 3c1 0 2 3 2.5 4.5S6 9.5 6 10c1 2.5 3.5 5 6 6 .5 0 1.5-2 2.5-1.5S19 16 19 17s-2 3-3.5 3C9 20 2 13 2 6.5 2 5 4 3 5 3z" fill="var(--gold)"/></svg>01742 918576</li>
      <li><svg class="contact-icon" viewBox="0 0 22 22"><rect x="1" y="1" width="20" height="20" rx="3" fill="var(--gold)"/><path d="M5 7h12v8H5z" fill="none" stroke="#fff" stroke-width="1.4"/><path d="M5 7l6 5 6-5" fill="none" stroke="#fff" stroke-width="1.4"/></svg>d.mallow@plumvora.example</li>
      <li><svg class="contact-icon" viewBox="0 0 22 22"><circle cx="11" cy="11" r="10" fill="var(--gold)"/><ellipse cx="11" cy="11" rx="4" ry="8" fill="none" stroke="#fff" stroke-width="1.3"/><path d="M3 11h16" stroke="#fff" stroke-width="1.3"/></svg>www.plumvora.example</li>
    </ul>

    <div class="social-links">
      <span class="social-dot"></span>
      <span class="social-dot"></span>
      <span class="social-dot"></span>
    </div>
  </div>
</body>
</html>
```